Elegant Business Card for Technology Company

Client is a supplier of innovative industrial communications and automation equipment since 2002. This contest is to gather fresh ideas for a redesign of the existing business card. Client is looking for design that best communicates tagline "Industrial Networking and Computing Specialist".

Design submissions should look modern, clean, elegant and professional. It should not be cluttered. Use white as the primary colour. Orange and black as secondary colour. Refer to jpeg File 1 on the current design.

Fonts used by Client used include Arial Regular, Arial Black, Roboto Regular, Roboto Black and Lato.

The winning design will be sent for offset printing using super white 250gsm artcard paper (open for suggestions).

Target Market(s)

System Engineers, Project Managers, Purchasing Managers from companies providing engineering services for Smart Cities.

Industry/Entity Type

Information Technology

Contact Information for Business Card

Refer to PDF File 3 for Business Card Details. Priority of short contact information would be as follows Name > Job Title > Email > Mobile > Web > Tel > Fax > Business Address >UEN (UEN represents company registration number)

Font styles to use
Sans Serif

Colors
ffffff
f37122
000000
5c5c5c

Requirements
Must have
• Refer to AI File 2 (Company Logo) & PDF File 3 (Information on Namecard)
Should not have
• No QR codes
• No Social Media Icons
• Do not create full Black or Orange colour background

```html
<!DOCTYPE html>
<html lang="en">
<head>
<meta charset="utf-8">
<title>Kestrel Asia Pacific – Business Card</title>
<link rel="stylesheet" href="https://fonts.googleapis.com/css2?family=Lato:wght@400;700&display=swap">
<style>
  :root {
    --orange: #ec6b12;
    --black: #1a1a1a;
    --ink: #222222;
    --paper: #ffffff;
    --backdrop: #ebebeb;
  }
  html, body {
    margin: 0;
    padding: 0;
    width: 1030px;
    height: 1200px;
    overflow: hidden;
    background: var(--backdrop);
    font-family: "Lato", Arial, sans-serif;
    color: var(--ink);
  }
  .canvas { position: relative; width: 1030px; height: 1200px; }
  .card {
    position: absolute;
    left: 120px;
    width: 774px;
    height: 470px;
    background: var(--paper);
    box-shadow: 0 2px 10px rgba(0,0,0,0.08);
    overflow: hidden;
  }
  .card--front { top: 108px; }
  .card--back { top: 630px; }
  .card svg.swoosh { position: absolute; left: 0; top: 0; }

  .services {
    position: absolute;
    left: 170px;
    top: 156px;
    margin: 0;
    padding: 0;
    list-style: none;
    font-size: 27.5px;
    line-height: 36.8px;
  }
  .services li { position: relative; padding-left: 20px; }
  .services li::before {
    content: "";
    position: absolute;
    left: 0;
    top: 15px;
    width: 9px;
    height: 9px;
    border-radius: 50%;
    background: var(--orange);
  }
  .tagline {
    position: absolute;
    left: 0;
    right: 0;
    top: 407px;
    margin: 0;
    text-align: center;
    font-size: 30.5px;
    font-weight: 400;
  }
  .front-rule {
    position: absolute;
    left: 0; right: 0; bottom: 0;
    height: 8px;
    background: var(--orange);
  }

  .company {
    position: absolute;
    left: 48px;
    top: 108px;
    margin: 0;
    font-size: 27px;
    font-weight: 700;
    color: var(--black);
    letter-spacing: -0.2px;
  }

  .address {
    position: absolute;
    left: 48px;
    top: 204px;
    margin: 0;
    font-style: normal;
    font-size: 21px;
    line-height: 26px;
  }
  .contacts {
    position: absolute;
    left: 48px;
    top: 266px;
    margin: 0;
    padding: 0;
    list-style: none;
    font-size: 21px;
    line-height: 26.3px;
  }
  .contacts li { display: flex; align-items: center; }
  .contacts svg { width: 18px; height: 18px; margin-right: 12px; fill: var(--orange); }
  .uen { position: absolute; left: 48px; top: 380px; font-size: 15px; }

  .person { position: absolute; right: 46px; top: 202px; text-align: right; }
  .person__name { margin: 0; font-size: 30px; font-weight: 400; color: var(--orange); line-height: 36px; }
  .person__title { margin: 0; font-size: 21px; line-height: 30px; }

  .web {
    position: absolute;
    right: 46px;
    top: 430px;
    font-size: 21px;
    letter-spacing: 2px;
    color: var(--paper);
  }
</style>
</head>
<body>
<div class="canvas">

  <section class="card card--front">
    <svg class="swoosh" width="774" height="470" viewBox="0 0 774 470" aria-hidden="true">
      <path fill="var(--black)" d="M0 0 H774 V28 H650 C420 30 180 48 0 78 Z"/>
      <path fill="var(--orange)" d="M0 84 C200 52 420 35 650 32 C420 39 200 70 0 116 Z"/>
    </svg>
    <ul class="services">
      <li>Industrial Ethernet / Wireless / Cellular</li>
      <li>Industrial and Embedded Computing</li>
      <li>Serial / Fieldbus Connectivity</li>
      <li>IP Video Surveillance</li>
      <li>Remote Automation</li>
    </ul>
    <p class="tagline">Industrial Networking and Computing Specialist</p>
    <div class="front-rule"></div>
  </section>

  <section class="card card--back">
    <svg class="swoosh" width="774" height="470" viewBox="0 0 774 470" aria-hidden="true">
      <path fill="var(--black)" d="M0 434 H600 C680 422 740 404 774 386 V470 H0 Z"/>
      <path fill="var(--orange)" d="M120 431 C420 426 650 400 774 345 V378 C640 414 420 428 120 431 Z"/>
    </svg>

    <p class="company">Kestrel Asia Pacific Pte Ltd</p>

    <address class="address">24 Harbour Link, Link Techpark<br>#05-12, Singapore 409871</address>

    <ul class="contacts">
      <li><svg viewBox="0 0 24 24"><path d="M6.6 10.8a15 15 0 0 0 6.6 6.6l2.2-2.2c.3-.3.7-.4 1-.2 1.1.4 2.3.6 3.6.6.6 0 1 .4 1 1V20c0 .6-.4 1-1 1A17 17 0 0 1 3 4c0-.6.4-1 1-1h3.5c.6 0 1 .4 1 1 0 1.3.2 2.5.6 3.6.1.3 0 .7-.2 1z"/></svg>+65 6123 4501</li>
      <li><svg viewBox="0 0 24 24"><path d="M7 2h10a1 1 0 0 1 1 1v18a1 1 0 0 1-1 1H7a1 1 0 0 1-1-1V3a1 1 0 0 1 1-1zm1 2v14h8V4z"/></svg>+65 9123 4567</li>
      <li><svg viewBox="0 0 24 24"><path d="M7 3h8l2 2v4H7zM3 10h18v8h-3v-3H6v3H3zM7 16h10v5H7z"/></svg>+65 6123 4502</li>
      <li><svg viewBox="0 0 24 24"><path d="M2 5h20v14H2zm2 2v.5l8 5 8-5V7l-8 5z"/></svg>sales@kestrel-ind.sg</li>
    </ul>
    <div class="uen">UEN No.: 200305512K</div>

    <div class="person">
      <h1 class="person__name">Daniel Lim&nbsp; 林丹尼</h1>
      <p class="person__title">Sales Manager</p>
    </div>

    <div class="web">www.kestrel-ind.sg</div>
  </section>

</div>
</body>
</html>
```